Camp Thornbrook 2021 Magazine Design

We are for someone to design our annual magazine/newsletter. This is a print newsletter that is a total of 20 pages. It will need to be designed in a way that is easy to share with our printers. The designer will need to be someone who is creative and easy to work with.
For those interested in this project we ask that you design 4 to 6 pages for us to view. Once we select the designer we will want the rest created in a two-week time span. For those submitting a bid please include front cover, theme & dates, mission & vision, and Make the Difference.

This link will provide the layout of the newsletter https://files.parcelvault.example/doc/7qzRk2LmVt9XwPa4NbHc6DsYe3FuJg8KoTiW5rQx/edit?share=1.

This link will provide you with the pictures that are needed and a few documents https://files.parcelvault.example/folders/4TpWx8QnRb2ZyLc7MfVd5HsJ?share=1

Details:
20 pages long (including covers)
8.5 x 11

Please message me if you need any further details.

Target Market(s)

Our alumni base. Covers all ages

Requirements
Must have
• Spelled out in document
Nice to have
• Spelled out in document
Should not have
• Spelled out in document

```html
<!DOCTYPE html>
<html lang="en">
<head>
<meta charset="utf-8">
<title>Camp Thornbrook – 2021 Theme and Dates</title>
<link rel="stylesheet" href="https://fonts.googleapis.com/css2?family=Bebas+Neue&family=Open+Sans:wght@400;700&display=swap">
<style>
  :root {
    --teal: #5aa59a;
    --teal-dark: #2f6660;
    --orange: #f3a05f;
    --tan: #d9c48f;
    --ink: #3d3a2e;
    --olive: #4f4a36;
    --rule: #9a9a9a;
    --frame: #cfcfcf;
    --paper: #ffffff;
  }
  * { margin: 0; padding: 0; box-sizing: border-box; }
  html, body { width: 1200px; height: 1000px; overflow: hidden; background: var(--paper); }
  body { position: relative; font-family: "Open Sans", sans-serif; color: var(--ink); }

  .page { position: absolute; top: 124px; width: 556px; height: 719px; border: 1px solid var(--frame); background: var(--paper); }
  .page--left { left: 36px; }
  .page--right { left: 608px; }

  .running-head { position: absolute; left: 33px; top: 38px; font-family: "Bebas Neue", sans-serif; font-size: 22px; color: var(--olive); letter-spacing: 0.2px; }
  .running-url { position: absolute; right: 33px; top: 45px; font-size: 11px; color: var(--olive); }
  .head-rule { position: absolute; left: -1px; right: -1px; top: 72px; height: 4px; background: var(--orange); }
  .foot-rule { position: absolute; top: 690px; width: 57px; height: 4px; background: var(--orange); }
  .page--left .foot-rule { left: -1px; }
  .page--right .foot-rule { right: -1px; }
  .folio { position: absolute; top: 701px; font-family: "Bebas Neue", sans-serif; font-size: 15px; color: var(--olive); }
  .page--left .folio { left: 32px; }
  .page--right .folio { right: 32px; }

  .section-title { position: absolute; left: 33px; top: 94px; font-family: "Bebas Neue", sans-serif; font-weight: 400; font-size: 26px; color: var(--teal); letter-spacing: 0.2px; }
  .theme-art { position: absolute; left: 94px; top: 129px; width: 368px; height: 368px;
    background: linear-gradient(170deg, #d6d6d6 0%, #a9a9a9 35%, #c99a8a 60%, #7a6a6e 80%, #3a3a3a 100%); }
  .divider-band { position: absolute; left: 33px; top: 532px; width: 490px; height: 18px; background: var(--tan); }
  .registration { position: absolute; left: 0; right: 0; top: 575px; text-align: center; font-size: 16.5px; line-height: 22.6px; color: var(--olive); }
  .registration b { font-weight: 700; }

  .grid-table { position: absolute; left: 33px; width: 490px; border-collapse: collapse; table-layout: fixed; font-size: 10px; }
  .grid-table th { background: var(--teal); color: #fff; font-family: "Bebas Neue", sans-serif; font-weight: 400; font-size: 17px; height: 22px; line-height: 22px; border-left: 1px solid #fff; }
  .grid-table th:first-child { border-left: none; }
  .grid-table td { height: 12.9px; line-height: 12px; text-align: center; border-bottom: 1px solid var(--rule); border-left: 1px solid var(--rule); color: var(--ink); }
  .grid-table td:first-child { border-left: none; }
  .sessions { top: 129px; }
  .groups { top: 293px; }

  .activities-bar { position: absolute; left: 33px; top: 378px; width: 490px; height: 23px; background: var(--teal); color: #fff; text-align: center; font-family: "Bebas Neue", sans-serif; font-size: 17px; line-height: 23px; }
  .activity { position: absolute; width: 110px; margin-left: -55px; text-align: center; font-size: 10.5px; line-height: 12px; color: var(--ink); }
  .activity .glyph { display: block; width: 42px; height: 42px; margin: 0 auto 5px; border-radius: 8px; }
  .activity .new { font-weight: 700; display: block; }
  .more { position: absolute; left: -8px; width: 556px; top: 648px; text-align: center; font-size: 10.5px; font-weight: 700; }
</style>
</head>
<body>

<section class="page page--left">
  <div class="running-head">2021 Theme and Dates</div>
  <div class="running-url">https://www.campthornbrook.org/</div>
  <div class="head-rule"></div>

  <h2 class="section-title">Registration and Other Information</h2>
  <div class="theme-art" role="img" aria-label="2021 camp theme artwork over a misty mountain landscape at dusk"></div>
  <div class="divider-band" role="img" aria-label="Tan zigzag divider"></div>

  <p class="registration">
    Registration begins on <b>January 1, 2021</b><br>
    Register online at <b>campthornbrook.org</b><br>
    <b>Super Early Bird Discount</b> ($20) if registered before April 1st<br>
    <b>Early Bird Discount</b> ($10) if registered in the month of April
  </p>

  <div class="foot-rule"></div>
  <div class="folio">6</div>
</section>

<section class="page page--right">
  <div class="running-head">2021 Theme and Dates</div>
  <div class="running-url">https://www.campthornbrook.org/</div>
  <div class="head-rule"></div>

  <table class="grid-table sessions">
    <colgroup><col style="width:163px"><col style="width:163px"><col style="width:164px"></colgroup>
    <thead><tr><th>Session</th><th>Date</th><th>Price $</th></tr></thead>
    <tbody>
      <tr><td>Session 1</td><td>May 30 - June 5</td><td>285</td></tr>
      <tr><td>Short Session 1</td><td>May 30 - June 2</td><td>175</td></tr>
      <tr><td>Session 2</td><td>June 6 - June 17</td><td>425</td></tr>
      <tr><td>Session 2B</td><td>June 6 - June 12</td><td>285</td></tr>
      <tr><td>Session 3</td><td>June 27 - July 8</td><td>425</td></tr>
      <tr><td>Session 3B</td><td>June 27 - July 3</td><td>285</td></tr>
      <tr><td>Session 4</td><td>July 11 - July 22</td><td>425</td></tr>
      <tr><td>Session 4B</td><td>July 11 - July 17</td><td>285</td></tr>
      <tr><td>Session 5</td><td>July 25 - July 31</td><td>285</td></tr>
      <tr><td>Short Session 2</td><td>July 25 - July 28</td><td>175</td></tr>
    </tbody>
  </table>

  <table class="grid-table groups">
    <colgroup><col style="width:163px"><col style="width:327px"></colgroup>
    <thead><tr><th>Group</th><th>Age</th></tr></thead>
    <tbody>
      <tr><td>1</td><td>8 - 10 Years</td></tr>
      <tr><td>2</td><td>11 - 12 Years</td></tr>
      <tr><td>3</td><td>13 - 14 Years</td></tr>
      <tr><td>4</td><td>15 - 18 Years</td></tr>
    </tbody>
  </table>

  <div class="activities-bar">Activities</div>

  <div class="activity" style="left:91px;top:412px"><span class="glyph" role="img" aria-label="Archery tag icon" style="background:var(--tan)"></span>Archery Tag</div>
  <div class="activity" style="left:181px;top:412px"><span class="glyph" role="img" aria-label="Blob icon" style="background:var(--orange)"></span>Blob</div>
  <div class="activity" style="left:270px;top:412px"><span class="glyph" role="img" aria-label="Horseback riding icon" style="background:var(--olive)"></span>Horseback Riding</div>
  <div class="activity" style="left:376px;top:412px"><span class="glyph" role="img" aria-label="Hiking icon" style="background:var(--teal)"></span>Hiking</div>
  <div class="activity" style="left:469px;top:412px"><span class="glyph" role="img" aria-label="Gaga ball icon" style="background:var(--teal-dark)"></span>Gaga Ball</div>

  <div class="activity" style="left:91px;top:486px"><span class="glyph" role="img" aria-label="Golden goal icon" style="background:var(--olive)"></span>Golden Goal<span class="new">(New)</span></div>
  <div class="activity" style="left:181px;top:486px"><span class="glyph" role="img" aria-label="Rappelling icon" style="background:var(--tan)"></span>Rappelling</div>
  <div class="activity" style="left:270px;top:486px"><span class="glyph" role="img" aria-label="Archery icon" style="background:var(--orange)"></span>Archery</div>
  <div class="activity" style="left:376px;top:486px"><span class="glyph" role="img" aria-label="Hatchet throwing icon" style="background:var(--teal-dark)"></span>Hatchet Throwing<span class="new">(New)</span></div>
  <div class="activity" style="left:469px;top:486px"><span class="glyph" role="img" aria-label="Basketball icon" style="background:var(--olive)"></span>Basketball</div>

  <div class="activity" style="left:154px;top:565px"><span class="glyph" role="img" aria-label="Arts and crafts icon" style="background:var(--teal)"></span>Arts and Crafts</div>
  <div class="activity" style="left:270px;top:565px"><span class="glyph" role="img" aria-label="9 square in the air icon" style="background:var(--teal)"></span>9 Square in the Air</div>
  <div class="activity" style="left:375px;top:565px"><span class="glyph" role="img" aria-label="Swimming icon" style="background:var(--tan)"></span>Swimming</div>

  <p class="more">And much more!</p>

  <div class="foot-rule"></div>
  <div class="folio">7</div>
</section>

</body>
</html>
```